Home Page and One Inside Page Needed for Engine Modify Site

Website that sells kits to modify and enhance your car engine performance. I don't like direction / design of current site at http://www.vaxorspeedlab.com.php53-17.ord1-1.draftpreviewbox.com/

I want something modern. Something that shows power and performance.

I need home page and one inside page.

Keep blues and blacks and unfortunately that is their logo we have to work with. But this site needs WOW factor.

YOU DO NOT HAVE PERMISSION TO WORK OR SPEAK TO CLIENT DIRECTLY AND MUST WORK THROUGH ME.

```html
<!DOCTYPE html>
<html lang="en">
<head>
<meta charset="utf-8">
<title>Vaxor Speed Lab</title>
<link href="https://fonts.googleapis.com/css2?family=Fredoka:wght@500;600&family=Lexend:wght@300;400;600&family=Ubuntu:wght@400&display=swap" rel="stylesheet">
<style>
  :root {
    --blue: #5e9bfb;
    --headline-blue: #5893f4;
    --ink: #4f4f4f;
    --white: #ffffff;
    --black: #000000;
    --steel-light: #f4f5f7;
    --steel-mid: #dde1e5;
    --steel-edge: #e4e7ea;
  }
  * { margin: 0; padding: 0; box-sizing: border-box; }
  html, body { width: 1200px; height: 900px; overflow: hidden; background: var(--white); }
  body { position: relative; font-family: "Ubuntu", sans-serif; }

  .body-copy {
    position: absolute;
    font-size: 14.5px;
    line-height: 22px;
    color: var(--ink);
  }
  .feature-prev .body-copy { left: 146px; top: -2px; width: 552px; }

  .product-shot {
    position: absolute;
    border: 1px solid var(--steel-edge);
    border-radius: 10px;
    background: linear-gradient(160deg, var(--steel-light) 0%, var(--steel-mid) 100%);
  }
  .feature-prev .product-shot { left: 720px; top: -12px; width: 350px; height: 104px; }
  .feature .product-shot { left: 148px; top: 172px; width: 335px; height: 230px; }

  .feature .headline {
    position: absolute; left: 495px; top: 170px;
    font-family: "Fredoka", sans-serif; font-weight: 600;
    font-size: 31.6px; letter-spacing: 0.5px;
    color: var(--headline-blue); text-transform: uppercase;
  }
  .feature .body-copy { left: 496px; top: 228px; width: 560px; }

  .cta-band {
    position: absolute; left: 0; top: 475px; width: 1200px; height: 69px;
    background: var(--blue);
  }
  .cta-text {
    position: absolute; left: 145px; top: 23px;
    font-family: "Lexend", sans-serif; font-weight: 600; font-size: 17.7px;
    color: var(--white); text-transform: uppercase; letter-spacing: 0.3px;
  }
  .cta-button {
    position: absolute; left: 870px; top: 18px; width: 182px; height: 34px;
    background: var(--white); border-radius: 8px;
    font-family: "Lexend", sans-serif; font-weight: 600; font-size: 19.5px;
    color: var(--blue); text-align: center; line-height: 34px;
    text-transform: uppercase; text-decoration: none;
  }

  .site-footer {
    position: absolute; left: 0; top: 547px; width: 1200px; height: 353px;
    background: var(--black); color: var(--white);
    font-family: "Lexend", sans-serif;
  }
  .footer-title { position: absolute; top: 43px; font-weight: 300; font-size: 18px; text-transform: uppercase; }
  .sitemap .footer-title { left: 144px; }
  .sitemap ul { position: absolute; left: 146px; top: 84px; list-style: none; }
  .sitemap li { font-weight: 600; font-size: 14px; line-height: 24.5px; text-transform: uppercase; }
  .sitemap a { color: var(--white); text-decoration: none; }

  .contact { position: absolute; right: 145px; top: 0; text-align: right; }
  .contact .footer-title { right: 0; white-space: nowrap; letter-spacing: 0.3px; }
  .contact address {
    position: absolute; right: 0; top: 84px; white-space: nowrap;
    font-style: normal; font-weight: 300; font-size: 14.3px; line-height: 24.5px; text-transform: uppercase;
  }
  .contact .email { display: block; margin-top: 24.5px; font-weight: 600; font-size: 14px; }
</style>
</head>
<body>
  <section class="feature-prev">
    <p class="body-copy">cursus. Interdum et malesuada fames ac ante ipsum primis in faucibus. Suspendisse dictum convallis arcu sit amet semper. Maecenas ligula ligula, rhoncus nec ultrices</p>
    <div class="product-shot" role="img" aria-label="Chrome engine crankshaft assembly"></div>
  </section>

  <section class="feature">
    <div class="product-shot" role="img" aria-label="Chrome V8 engine block with exhaust headers"></div>
    <h2 class="headline">Some form of headline here</h2>
    <p class="body-copy">Lorem ipsum dolor sit amet, consectetur adipiscing elit. Donec gravida turpis id justo adipiscing egestas. Fusce sit amet ultricies nisi. Integer fringilla, elit a hendrerit euismod, orci nibh suscipit neque, sed volutpat neque nulla vel elit. Morbi eleifend sapien sapien, a porta nisl placerat nec. Aliquam ut ligula viverra, porttitor justo id, semper quam. Pellentesque vel placerat massa. Praesent id tincidunt mi. Cras porta neque id lectus rhoncus, et varius enim luctus. Quisque commodo eleifend ipsum id cursus. Interdum et malesuada fames ac ante ipsum primis in faucibus. Suspendisse dictum convallis arcu sit amet semper. Maecenas ligula ligula, rhoncus nec ultrices</p>
  </section>

  <section class="cta-band">
    <p class="cta-text">Let’s have a chat to find out more about what we can do for you</p>
    <a class="cta-button" href="#contact">Contact us</a>
  </section>

  <footer class="site-footer">
    <nav class="sitemap">
      <h3 class="footer-title">Site map</h3>
      <ul>
        <li><a href="#">Home</a></li>
        <li><a href="#">About</a></li>
        <li><a href="#">How it works</a></li>
        <li><a href="#">Resources</a></li>
        <li><a href="#">Product</a></li>
        <li><a href="#">Contact us</a></li>
      </ul>
    </nav>
    <div class="contact" id="contact">
      <h3 class="footer-title">Vaxorspeedlab</h3>
      <address>
        48 Fenwick Lane Dallas, TX 75201<br>
        Phone: (555) 014 7720<br>
        Fax: (555) 014 7721<br>
        M–F 9–6
        <span class="email">Email: info@vaxorspeedlab.com</span>
      </address>
    </div>
  </footer>
</body>
</html>
```